Irrigation Business needs their business cards modernised and revamped

I would like to keep my current logo, colours and revamp the format of the card.

I would like the card to be clean yet important.

Im not sure if you include texture but i would like the named logo to be indented into the card etc.

show me something alive and free something thats clinical to the point yet has a feel of achievement. i would like people to go nice card.

Target Market(s)

high end clients, corporate, sports field manger, the guys that make the decisions

Industry/Entity Type

Business

Contact Information for Business Card

nformation to be included

Dean Harlow (Director)
0487305526
dean@kolvat.biz
www.kestonfieldworks.com

instagram logo
google logo
facebook logo

Colors

Designer to choose colors to be used in the design.

Requirements
Nice to have
• indentations a really nice feel to the card good texture

```html
<!DOCTYPE html>
<html lang="en">
<head>
<meta charset="utf-8">
<title>Keston Fieldworks – Business Card</title>
<link rel="stylesheet" href="https://fonts.googleapis.com/css2?family=Montserrat:wght@400;700&family=Oswald:wght@500&display=swap">
<style>
  :root {
    --backdrop: #e6e8eb;
    --card: #ffffff;
    --brand-blue: #2f66ad;
    --accent-blue: #3aa6db;
    --text-grey: #6f7378;
    --faint: #f3f3f3;
    --social: #9aa3ad;
  }
  * { box-sizing: border-box; margin: 0; padding: 0; }
  html, body { width: 1200px; height: 900px; overflow: hidden; }
  body {
    background: var(--backdrop);
    font-family: "Montserrat", sans-serif;
    position: relative;
  }
  .card {
    position: absolute;
    left: 250px;
    width: 700px;
    height: 400px;
    background: var(--card);
    box-shadow: 0 10px 30px rgba(0,0,0,.12);
    overflow: hidden;
  }
  .card--front { top: 35px; }
  .card--back { top: 465px; }

  /* Front */
  .front__backdrop-circle {
    position: absolute;
    right: -40px;
    top: 90px;
    width: 330px;
    height: 330px;
    border-radius: 50%;
    background: var(--faint);
  }
  .brand {
    position: absolute;
    left: 0; right: 0;
    top: 150px;
    display: flex;
    align-items: center;
    justify-content: center;
    gap: 16px;
  }
  .brand__dot {
    width: 46px; height: 46px;
    border-radius: 50%;
    background: var(--accent-blue);
  }
  .brand__name {
    font-weight: 700;
    font-size: 36px;
    color: var(--brand-blue);
    letter-spacing: .5px;
  }
  .social {
    position: absolute;
    left: 0; right: 0;
    top: 262px;
    display: flex;
    justify-content: center;
    gap: 10px;
  }
  .social__item {
    width: 20px; height: 20px;
    border-radius: 4px;
    background: var(--social);
  }

  /* Back */
  .identity {
    position: absolute;
    right: 410px;
    top: 150px;
    text-align: right;
  }
  .identity__name {
    font-family: "Oswald", sans-serif;
    font-weight: 500;
    font-size: 40px;
    line-height: 1;
    color: var(--brand-blue);
    text-transform: uppercase;
    letter-spacing: .5px;
  }
  .identity__role {
    font-size: 18px;
    color: var(--text-grey);
    margin-top: 8px;
  }
  .divider {
    position: absolute;
    left: 315px;
    top: 145px;
    width: 2px;
    height: 95px;
    background: var(--accent-blue);
  }
  .contact {
    position: absolute;
    left: 345px;
    top: 150px;
    list-style: none;
  }
  .contact__item {
    display: flex;
    align-items: center;
    gap: 14px;
    font-size: 17px;
    color: var(--text-grey);
    height: 28px;
    letter-spacing: .3px;
  }
  .contact__icon { width: 16px; height: 16px; flex: none; }
</style>
</head>
<body>

<section class="card card--front" aria-label="Card front">
  <div class="front__backdrop-circle"></div>
  <div class="brand">
    <span class="brand__dot"></span>
    <span class="brand__name">Keston Fieldworks</span>
  </div>
  <div class="social" aria-label="Social media">
    <span class="social__item"></span>
    <span class="social__item"></span>
    <span class="social__item"></span>
  </div>
</section>

<section class="card card--back" aria-label="Card back">
  <div class="identity">
    <p class="identity__name">Dean Harlow</p>
    <p class="identity__role">Director</p>
  </div>
  <div class="divider"></div>
  <ul class="contact">
    <li class="contact__item">
      <svg class="contact__icon" viewBox="0 0 16 16" aria-hidden="true"><path fill="#2f66ad" d="M3.5 1.5l2.5 3-1.5 1.5c.8 1.8 2.2 3.2 4 4l1.5-1.5 3 2.5-1.5 2.5C7 13 3 9 1 3.2z"/></svg>
      <span>0487305526</span>
    </li>
    <li class="contact__item">
      <svg class="contact__icon" viewBox="0 0 16 16" aria-hidden="true"><rect x="1" y="3" width="14" height="10" fill="#2f66ad"/><path d="M1.5 3.5L8 9l6.5-5.5" stroke="#fff" stroke-width="1.2" fill="none"/></svg>
      <span>dean@kolvat.biz</span>
    </li>
    <li class="contact__item">
      <svg class="contact__icon" viewBox="0 0 16 16" aria-hidden="true"><g fill="none" stroke="#2f66ad" stroke-width="1.2"><circle cx="8" cy="8" r="6.5"/><ellipse cx="8" cy="8" rx="3" ry="6.5"/><path d="M1.5 8h13M2.5 4.8h11M2.5 11.2h11"/></g></svg>
      <span>www.kestonfieldworks.com</span>
    </li>
  </ul>
</section>

</body>
</html>
```